NEW Modern Sleek Business Card for VR Language Startup

Our startup is using VR to lead the next wave of world language education. We need a two-sided business card that introduces the larger organization (Brightloom Language Inc) and our contact info on one side and shows the product, Glimwoorld, on the other side.

Side 1 (contact info)= Brightloom Logo and Contact info (name, title, phone, email)

Side 2 (product)= Glimworld logo, text, and website
Text= Culturally Immersive Language Learning Games
Website= www.glimworld-play.com

Target Market(s)

Education, Technology

Contact Information for Business Card

Contact info will be updated upon approval of the design. For now, put this as a placeholder.

Perry Dunmore
Founder & CEO
pdunmore@quillpost-mail.net
(555)-014-2286

Font styles to use
Other font styles liked:
• Gibson and Century Gothic are the brand fonts

Requirements
Nice to have
• I would love to see cohesion between the design and colors of the two logos. I have attached a few business card designs that I like, so you can get a feel for my preferred style.

```html
<!DOCTYPE html>
<html lang="en">
<head>
<meta charset="utf-8">
<title>Brightloom Language – Business Card</title>
<link rel="stylesheet" href="https://fonts.googleapis.com/css2?family=Lato:wght@400;700;900&display=swap">
<style>
  :root {
    --backdrop: #3b3c40;
    --card: #05070a;
    --cyan: #3cc4ee;
    --violet: #6a6fc9;
    --coral: #f0433c;
    --orange: #f06a2a;
    --gold: #e8c21c;
    --white: #ffffff;
    --grey: #8d8f94;
  }
  * { box-sizing: border-box; margin: 0; padding: 0; }
  html, body {
    width: 1200px; height: 900px; overflow: hidden;
    background: var(--backdrop);
    font-family: "Lato", Arial, sans-serif;
  }
  .canvas { position: relative; width: 1200px; height: 900px; }
  .card {
    position: absolute;
    width: 600px; height: 343px;
    background: var(--card);
    border-radius: 26px;
    box-shadow: 0 18px 40px rgba(0,0,0,.45);
    overflow: hidden;
  }

  /* Product side */
  .card--product { left: 90px; top: 90px; }
  .product__brand {
    position: absolute; left: 0; right: 0; top: 112px;
    display: flex; align-items: center; justify-content: center; gap: 14px;
  }
  .product__dot { width: 26px; height: 26px; border-radius: 50%; background: var(--cyan); }
  .product__name { font-size: 46px; font-weight: 700; color: var(--cyan); letter-spacing: .5px; }
  .product__tagline {
    position: absolute; left: 0; right: 0; top: 200px;
    text-align: center; font-size: 19px; color: var(--cyan);
  }
  .product__web {
    position: absolute; left: 0; right: 0; top: 258px;
    display: flex; align-items: center; justify-content: center; gap: 10px;
    font-size: 15px; color: var(--grey); letter-spacing: .5px;
  }

  /* Contact side */
  .card--contact { left: 510px; top: 470px; }
  .contact__brand {
    position: absolute; right: 42px; top: 58px;
    display: flex; align-items: center; gap: 12px;
  }
  .contact__dot { width: 24px; height: 24px; border-radius: 50%; background: var(--coral); }
  .contact__brandname { font-size: 28px; font-weight: 700; color: var(--white); letter-spacing: 1.5px; }
  .contact__rule {
    position: absolute; left: 50px; right: 30px; top: 184px;
    height: 2px; background: var(--gold);
  }
  .contact__person { position: absolute; left: 50px; top: 114px; }
  .contact__name { font-size: 30px; font-weight: 900; line-height: 1; }
  .contact__first { color: var(--coral); }
  .contact__last { color: var(--violet); }
  .contact__title { font-size: 17px; color: var(--white); margin-top: 6px; }
  .contact__list { position: absolute; left: 68px; top: 206px; list-style: none; }
  .contact__item {
    display: flex; align-items: center; gap: 12px;
    font-size: 17px; color: var(--white); margin-bottom: 10px;
  }
  .contact__icon { width: 18px; height: 18px; flex: none; }
</style>
</head>
<body>
<main class="canvas">

  <section class="card card--product" aria-label="Product side">
    <div class="product__brand">
      <span class="product__dot"></span>
      <span class="product__name">Glimworld</span>
    </div>
    <p class="product__tagline">Culturally Immersive Language Learning Games</p>
    <p class="product__web">
      <svg width="12" height="14" viewBox="0 0 12 14" aria-hidden="true"><path d="M1 1 L11 8 L6.5 8.5 L4 13 Z" fill="#5a8fe0"/></svg>
      www.glimworld-play.com
    </p>
  </section>

  <section class="card card--contact" aria-label="Contact side">
    <div class="contact__brand">
      <span class="contact__dot"></span>
      <span class="contact__brandname">Brightloom Language</span>
    </div>

    <div class="contact__person">
      <p class="contact__name"><span class="contact__first">Perry</span> <span class="contact__last">Dunmore</span></p>
      <p class="contact__title">Founder &amp; CEO</p>
    </div>

    <div class="contact__rule"></div>

    <ul class="contact__list">
      <li class="contact__item">
        <svg class="contact__icon" viewBox="0 0 24 24" aria-hidden="true"><path d="M6.6 10.8a15.1 15.1 0 0 0 6.6 6.6l2.2-2.2a1 1 0 0 1 1-.25 11.4 11.4 0 0 0 3.6.57 1 1 0 0 1 1 1V20a1 1 0 0 1-1 1A17 17 0 0 1 3 4a1 1 0 0 1 1-1h3.5a1 1 0 0 1 1 1c0 1.25.2 2.45.57 3.57a1 1 0 0 1-.25 1z" fill="var(--orange)"/></svg>
        (555)-014-2286
      </li>
      <li class="contact__item">
        <svg class="contact__icon" viewBox="0 0 24 24" aria-hidden="true"><rect x="2" y="5" width="20" height="14" rx="1.5" fill="var(--orange)"/><path d="M2.5 6 L12 13 L21.5 6" stroke="#05070a" stroke-width="1.6" fill="none"/></svg>
        pdunmore@quillpost-mail.net
      </li>
    </ul>
  </section>

</main>
</body>
</html>
```